Business Card Design For Office Furniture Clearance Company

Kestrel Office Clearance - our company name pretty much explains what we do, we clear offices for high end clients, mainly plc's and large international companies.

We require a nice looking business card that displays professionalism but without being too serious.

It would be nice to see just a little more than a conventional boring business card, make sure you add some flare.

Industry/Entity Type

Office Furniture

Contact Information for Business Card

CARD 1

Mark Holloway
Director
mark@kestrelofficeclearance.co.uk
m: 07700 153928

t: 01632 960418
www.kestrelofficeclearance.co.uk

Kestrel Office Clearance
Unit K4 B
2-8 Fenwick Lane
Bletchley
Milton Keynes
ZZ9 4QT

clearances at no cost… hard to beat a deal like that.

CARD 2

Peter Radford
Director
peter@kestrelofficeclearance.co.uk
m: 07700 382615

t: 01632 960418

Kestrel Office Clearance
Unit K4 B
2-8 Fenwick Lane
Bletchley
Milton Keynes
ZZ9 4QT

Font styles to use
Sans Serif

Requirements
Must have
• A white background - as we have a blue logo.
Nice to have
• Nice use of the logo - play around with this and dissect it.

```html
<!DOCTYPE html>
<html lang="en">
<head>
<meta charset="utf-8">
<title>Kestrel Office Clearance – Business Card</title>
<link rel="stylesheet" href="https://fonts.googleapis.com/css2?family=Open+Sans:wght@400;600;700&family=Arimo:wght@400&display=swap">
<style>
  :root {
    --stage: #2c2c2e;
    --brand-blue: #0b7cc3;
    --brand-blue-light: #1a93d8;
    --brand-blue-deep: #0a5f99;
    --card-white: #f7f7f7;
    --ink-white: #ffffff;
    --back-dark: #3b3b3d;
    --back-darker: #1f1f21;
    --tagline-grey: #b9b9bb;
  }
  * { box-sizing: border-box; margin: 0; padding: 0; }
  html, body { width: 1200px; height: 950px; overflow: hidden; }
  body { background: var(--stage); position: relative; font-family: "Open Sans", Arial, sans-serif; }

  .card {
    position: absolute;
    left: 260px;
    width: 680px;
    height: 400px;
    overflow: hidden;
    box-shadow: 0 10px 30px rgba(0,0,0,0.45);
  }
  .card--front { top: 50px; }
  .card--back { top: 500px; }
  .card__art { position: absolute; inset: 0; }

  .contact {
    position: absolute;
    left: 40px;
    top: 40px;
    color: var(--ink-white);
  }
  .contact__name { font-weight: 700; font-size: 30px; line-height: 1.1; }
  .contact__role { font-size: 17px; margin-top: 2px; }
  .contact__address {
    font-family: "Arimo", Arial, sans-serif;
    font-size: 17px;
    line-height: 1.3;
    margin-top: 34px;
  }
  .contact__list { list-style: none; margin-top: 16px; font-family: "Arimo", Arial, sans-serif; font-size: 17px; }
  .contact__list li { display: flex; align-items: center; gap: 8px; line-height: 1.45; white-space: nowrap; }
  .contact__list svg { width: 16px; height: 16px; flex: none; fill: var(--ink-white); }

  .brand-name {
    position: absolute;
    font-weight: 600;
    font-size: 16px;
    text-align: center;
    white-space: nowrap;
  }
  .brand-name--front { left: 460px; width: 200px; top: 338px; color: var(--brand-blue); }
  .brand-name--back { left: 0; width: 680px; top: 272px; color: var(--ink-white); font-size: 18px; }

  .tagline {
    position: absolute;
    right: 36px;
    bottom: 40px;
    font-size: 16px;
    color: var(--tagline-grey);
    white-space: nowrap;
  }
</style>
</head>
<body>

<section class="card card--front" aria-label="Business card front">
  <svg class="card__art" viewBox="0 0 680 400" aria-hidden="true">
    <defs>
      <linearGradient id="blueField" x1="0" y1="0" x2="1" y2="1">
        <stop offset="0" stop-color="var(--brand-blue-light)"/>
        <stop offset="1" stop-color="var(--brand-blue)"/>
      </linearGradient>
      <radialGradient id="whiteField" cx="0.5" cy="0.4" r="0.7">
        <stop offset="0" stop-color="#ffffff"/>
        <stop offset="1" stop-color="#e6e6e6"/>
      </radialGradient>
      <linearGradient id="markFill" x1="0" y1="0" x2="0" y2="1">
        <stop offset="0" stop-color="var(--brand-blue-light)"/>
        <stop offset="1" stop-color="var(--brand-blue-deep)"/>
      </linearGradient>
    </defs>
    <rect width="680" height="400" fill="url(#blueField)"/>
    <circle cx="600" cy="220" r="266" fill="none" stroke="var(--brand-blue-deep)" stroke-width="4"/>
    <circle cx="600" cy="220" r="255" fill="url(#whiteField)"/>
    <circle cx="560" cy="215" r="105" fill="url(#markFill)"/>
  </svg>

  <div class="contact">
    <p class="contact__name">Mark Holloway</p>
    <p class="contact__role">Director</p>
    <p class="contact__address">Kestrel Office Clearance<br>Unit K4 B, 2-8 Fenwick Lane<br>Ashcombe, Fernleigh<br>ZZ9 4QT</p>
    <ul class="contact__list">
      <li><svg viewBox="0 0 16 16"><path d="M3 2h3l1 3-2 1.5a9 9 0 0 0 4.5 4.5L11 9l3 1v3a1 1 0 0 1-1 1A12 12 0 0 1 2 3a1 1 0 0 1 1-1z"/></svg>01632 960418</li>
      <li><svg viewBox="0 0 16 16"><path d="M5 1h6a1 1 0 0 1 1 1v12a1 1 0 0 1-1 1H5a1 1 0 0 1-1-1V2a1 1 0 0 1 1-1zm0 2v9h6V3zm3 10a.8.8 0 1 0 0 1.6A.8.8 0 0 0 8 13z"/></svg>07700 153928</li>
      <li><svg viewBox="0 0 16 16"><path d="M1 4h14v9H1zm1.5 1 5.5 4 5.5-4z"/></svg>mark@kestrelofficeclearance.co.uk</li>
      <li><svg viewBox="0 0 16 16"><path d="M8 1a7 7 0 1 0 0 14A7 7 0 0 0 8 1zm0 1.5c.8 1 1.4 2.4 1.6 4H6.4C6.6 4.9 7.2 3.5 8 2.5zM2.6 7.5h2.4c.1 1.5.5 3 1.2 4.2A5.5 5.5 0 0 1 2.6 7.5zm8.4 0h2.4a5.5 5.5 0 0 1-3.6 4.2c.7-1.2 1.1-2.7 1.2-4.2zm-4.6 1h3.2c-.2 1.6-.8 3-1.6 4-.8-1-1.4-2.4-1.6-4z"/></svg>www.kestrelofficeclearance.co.uk</li>
    </ul>
  </div>

  <p class="brand-name brand-name--front">Kestrel Office Clearance</p>
</section>

<section class="card card--back" aria-label="Business card back">
  <svg class="card__art" viewBox="0 0 680 400" aria-hidden="true">
    <defs>
      <linearGradient id="darkField" x1="0" y1="0" x2="1" y2="1">
        <stop offset="0" stop-color="var(--back-dark)"/>
        <stop offset="1" stop-color="var(--back-darker)"/>
      </linearGradient>
    </defs>
    <rect width="680" height="400" fill="url(#darkField)"/>
    <circle cx="340" cy="165" r="90" fill="var(--card-white)"/>
  </svg>
  <p class="brand-name brand-name--back">Kestrel Office Clearance</p>
  <p class="tagline">clearances at no cost… hard to beat a deal like that.</p>
</section>

</body>
</html>
```